Facebook Header Design Project.

I'm supplying white and colored logos. The Facebook page already exists. URL = https://www.brindlepost.example/quillarc.studio The design should not be based on what's already there. Consider mobile implications of the design. This Design will form the designs of other social media headers. QuillArc is a web design | digital marketing company.

Target Market(s)

People interested in web design | digital marketing services.

Industry/Entity Type

QuillArc is a web design | digital marketing company. That should be clear in the design.

Colors
0054AA
0677BA
7BADD7
CADEEF
E8F1F8

Requirements
Must have
• Logo. Use Facebook header image dimension.
Nice to have
• Use a color scheme like the logo and feel free to add a color or two from the other side of the color whee.

```html
<!DOCTYPE html>
<html lang="en">
<head>
<meta charset="UTF-8">
<title>QuillArc — Web Design &amp; Digital Marketing Services</title>
<link rel="stylesheet" href="https://fonts.googleapis.com/css2?family=Josefin+Sans:wght@400;600;700&family=Arimo:wght@400&display=swap">
<style>
  :root {
    --page-bg: #0a1326;
    --banner-deep: #03256f;
    --banner-mid: #0a3a98;
    --banner-bright: #0b47b4;
    --frame-white: #ffffff;
    --text-white: #ffffff;
    --panel-border: #1d55c2;
    --photo-dark: #0c1a33;
    --photo-mid: #2a4a78;
    --photo-light: #7f9cc0;
    --accent-soft: rgba(123, 173, 215, 0.35);
    --accent-faint: rgba(123, 173, 215, 0.12);
  }

  * { box-sizing: border-box; margin: 0; padding: 0; }

  html, body {
    width: 1200px;
    height: 744px;
    overflow: hidden;
    background: var(--page-bg);
  }

  .canvas {
    position: relative;
    width: 1200px;
    height: 744px;
    background: var(--page-bg);
  }

  .cover-banner {
    position: absolute;
    left: 67px;
    top: 174px;
    width: 1066px;
    height: 396px;
    overflow: hidden;
    border: 2px solid var(--frame-white);
    background: linear-gradient(90deg, var(--banner-deep) 0%, var(--banner-mid) 55%, var(--banner-bright) 100%);
    font-family: "Josefin Sans", sans-serif;
    color: var(--text-white);
  }

  .dot-field {
    position: absolute;
    left: 10px;
    top: 198px;
    width: 50px;
    height: 186px;
    background: var(--accent-faint);
  }

  .ring-accent {
    position: absolute;
    left: 445px;
    top: 0;
    width: 120px;
    height: 118px;
  }

  .brand {
    position: absolute;
    left: 77px;
    top: 30px;
    display: flex;
    align-items: center;
    gap: 10px;
  }

  .brand-mark {
    width: 14px;
    height: 14px;
    border-radius: 50%;
    background: var(--text-white);
  }

  .brand-name {
    font-family: "Josefin Sans", sans-serif;
    font-weight: 700;
    font-size: 38px;
    line-height: 1;
    color: var(--text-white);
  }

  .headline {
    position: absolute;
    left: 74px;
    top: 108px;
    width: 490px;
    font-weight: 700;
    font-size: 44px;
    line-height: 53px;
    letter-spacing: 0;
    white-space: nowrap;
    text-transform: uppercase;
    z-index: 2;
  }

  .headline-rule {
    position: absolute;
    left: 77px;
    top: 268px;
    width: 228px;
    height: 4px;
    background: var(--text-white);
  }

  .intro {
    position: absolute;
    left: 77px;
    top: 285px;
    width: 440px;
    font-weight: 600;
    font-size: 14.5px;
    line-height: 19px;
    letter-spacing: -0.2px;
  }

  .social-row {
    position: absolute;
    left: 77px;
    top: 353px;
    display: flex;
    gap: 17px;
    list-style: none;
  }

  .social-row li {
    width: 24px;
    height: 24px;
    border-radius: 50%;
    background: var(--text-white);
  }

  .photo-panel {
    position: absolute;
    left: 575px;
    top: -2px;
    width: 462px;
    height: 347px;
    border: 5px solid var(--panel-border);
    border-top: none;
    background: linear-gradient(180deg, var(--photo-dark) 0%, var(--photo-mid) 45%, var(--photo-light) 62%, var(--photo-dark) 100%);
  }

  .panel-title {
    position: absolute;
    left: 134px;
    top: 124px;
    font-family: "Arimo", sans-serif;
    font-weight: 400;
    font-size: 38px;
    line-height: 44px;
    color: var(--text-white);
    text-transform: uppercase;
  }

  .corner-accent {
    position: absolute;
    right: 0;
    bottom: 0;
    width: 110px;
    height: 80px;
  }
</style>
</head>
<body>
  <main class="canvas">
    <section class="cover-banner" aria-label="QuillArc cover banner">
      <div class="dot-field" role="img" aria-label="Grid of small dots"></div>

      <svg class="ring-accent" viewBox="0 0 120 118" role="img" aria-label="Faint striped circle">
        <circle cx="60" cy="58" r="58" fill="rgba(123,173,215,0.3)"/>
      </svg>

      <div class="brand">
        <span class="brand-mark"></span>
        <span class="brand-name">QuillArc</span>
      </div>

      <div class="photo-panel" role="img" aria-label="Business people silhouetted in a glass office with digital marketing icons for video, blog, email, SEO, ads and growth charts">
        <p class="panel-title">Digital<br>Marketing</p>
      </div>

      <h1 class="headline">Web Design &amp;<br>Digital Marketing<br>Services</h1>
      <div class="headline-rule"></div>

      <p class="intro">Lorem Ipsum is simply dummy text of the printing and typesetting industry. Lorem has been the industry's standard dummy text ever since the 1500s</p>

      <ul class="social-row" aria-label="Social links">
        <li></li>
        <li></li>
        <li></li>
        <li></li>
      </ul>

      <svg class="corner-accent" viewBox="0 0 110 80" role="img" aria-label="Faint striped circle in the corner">
        <circle cx="80" cy="80" r="78" fill="rgba(123,173,215,0.22)"/>
      </svg>
    </section>
  </main>
</body>
</html>
```